Velour Detailing – Premium Automotive Detailing Studio Website Design

We're launching a premium automotive detailing studio called Velour Detailing, and we’re looking for a clean, minimal, and high-end website design (desktop + mobile version). The studio targets owners of luxury vehicles who care deeply about aesthetics, perfection, and exceptional service.
This project is about more than just showing services , it should feel like a luxury experience from the very first second. The design should be modern, minimalistic, elegant, and clearly aimed at an upscale market.
We’re looking for a designer who can translate our physical studio’s premium interior and architectural feel into a digital presence.
What we want the website to feel like:
Clean and modern
Professional and luxurious
Minimal and not cluttered
Light animations or transitions to add polish
Stylish and cinematic
Design freedom:
We trust your design direction. We are not providing strict color codes or layout instructions, we want you to create what you believe works best based on our brand positioning and target audience. Just keep it premium, modern, and well-organized.
What the website should include:
Hero section with a bold visual (image or video)
About the Studio — a few blocks explaining our story and focus on quality
Service Overview — clearly showing what we offer (detailing, ceramic coating, interior, etc.)
Gallery/Showcase — show off our work with cars, interior, and the space itself
Client Lounge Area — mention comfort, coffee, and waiting space
Testimonials — social proof from satisfied clients
Location & contact section — map, address, contact form
Footer, simple with nav, contact info, and optional social media
Target audience:
Owners of high-end vehicles (Valtrane, Korvel, etc.)
Car collectors and detailing enthusiasts
People looking for premium-level service and presentation
Brands/creators booking our photo studio

```html
<!DOCTYPE html>
<html lang="en">
<head>
<meta charset="utf-8">
<title>Velour Detailing – Testimonials, Location &amp; Contact</title>
<link href="https://fonts.googleapis.com/css2?family=Noto+Sans:wght@400;500&family=Poppins:wght@300;400;500;600&display=swap" rel="stylesheet">
<style>
  :root{
    --ink:#0d0d0d;
    --muted:#8a8a8a;
    --accent:#fbbf0a;
    --field:#f3f3f3;
    --footer-dark:#121212;
    --footer-light:#e4e4e6;
    --white:#ffffff;
  }
  *{margin:0;padding:0;box-sizing:border-box}
  html,body{width:1200px;height:1200px;overflow:hidden;background:var(--white)}
  .page{position:relative;width:1200px;height:1200px;font-family:"Noto Sans",sans-serif;color:var(--ink)}

  .testimonials{position:absolute;left:0;top:0;width:1200px;height:621px;
    background:linear-gradient(135deg,#fafafa 0%,#ececec 30%,#f7f7f7 55%,#e6e6e6 80%,#f4f4f4 100%)}
  .section-title{position:absolute;left:0;width:1200px;text-align:center;font-weight:400;font-size:53px;letter-spacing:0.5px;line-height:1}
  .testimonials .section-title{top:20px}

  .client-photo{position:absolute;width:255px;height:273px;border-radius:50%;top:144px}
  .client-photo.one{left:118px;background:radial-gradient(circle at 50% 40%,#c9a58b 0%,#8a6a55 35%,#3a4150 75%,#1f2635 100%)}
  .client-photo.two{left:472px;background:radial-gradient(circle at 50% 35%,#d6b7a3 0%,#a88d7d 30%,#4e6584 65%,#2c4468 100%)}
  .client-photo.three{left:828px;background:radial-gradient(circle at 50% 38%,#cfa990 0%,#9a7f70 30%,#8c8a8c 62%,#1c2236 100%)}

  .quote{position:absolute;top:461px;width:290px;text-align:center;font-size:13.3px;line-height:20px}
  .quote.one{left:94px}
  .quote.two{left:453px}
  .quote.three{left:809px}

  .rating{position:absolute;top:540px;display:flex;gap:6px}
  .rating.one{left:161px}
  .rating.two{left:527px}
  .rating.three{left:889px;top:538px}
  .rating svg{width:24px;height:18px;display:block}

  .location{position:absolute;left:0;top:621px;width:1200px;height:407px}
  .location .section-title{top:20px}

  .contact-line{position:absolute;left:204px;display:flex;align-items:center;font-family:"Poppins",sans-serif;font-weight:300;font-size:13.3px;color:var(--muted)}
  .contact-line svg{width:22px;height:22px;margin-right:21px}
  .contact-line.address{top:119px}
  .contact-line.mail{top:167px}

  .map{position:absolute;left:204px;top:219px;width:362px;height:170px;
    background:linear-gradient(120deg,#e6e6e6 0%,#dcdcdc 40%,#cfe8b4 55%,#e4e4e4 75%,#e9e9e9 100%)}

  .contact-form{position:absolute;left:622px;top:118px;width:375px}
  .field{position:absolute;left:0;width:375px;background:var(--field);font-family:"Poppins",sans-serif;font-size:12px;color:var(--muted);padding:12px 18px;letter-spacing:0.2px}
  .field.name{top:0;height:43px}
  .field.email{top:63px;height:43px}
  .field.message{top:125px;height:82px}
  .submit{position:absolute;left:0;top:226px;width:375px;height:44px;border-radius:22px;background:var(--accent);color:var(--white);font-family:"Poppins",sans-serif;font-size:16px;display:flex;align-items:center;justify-content:center}

  .site-footer{position:absolute;left:0;top:1028px;width:1200px;height:172px;background:var(--footer-dark);font-family:"Poppins",sans-serif}
  .brand-panel{position:absolute;left:0;top:0;width:227px;height:172px;background:var(--footer-light);display:flex;align-items:center;justify-content:center}
  .brand-name{font-family:"Poppins",sans-serif;font-weight:600;font-size:14px;letter-spacing:1px;color:var(--ink);text-align:center;line-height:1.3}
  .footer-col{position:absolute;top:22px;color:var(--white)}
  .footer-col h4{font-weight:500;font-size:14px;margin-bottom:9px}
  .footer-col li{list-style:none;font-size:11px;line-height:21.3px}
  .footer-col.one{left:349px}
  .footer-col.two{left:538px}
  .footer-col.three{left:727px}
  .social{position:absolute;left:906px;top:24px;display:flex;gap:14px}
  .social-item{display:flex;align-items:center;gap:5px;color:var(--white);font-size:11px;font-weight:400;line-height:1}
  .social-item::before{content:"";width:12px;height:12px;border-radius:50%;background:var(--white);flex:none}
</style>
</head>
<body>
<div class="page">

  <section class="testimonials">
    <h2 class="section-title">TESTIMONIALS</h2>

    <div class="client-photo one" role="img" aria-label="Portrait photo of a satisfied client"></div>
    <div class="client-photo two" role="img" aria-label="Portrait photo of a satisfied client"></div>
    <div class="client-photo three" role="img" aria-label="Portrait photo of a satisfied client"></div>

    <p class="quote one">lorem ipsum dolor sit amet, consectetur adipiscing elit,&nbsp; eiusmod tempor incididunt et dolore gna aliqua. enim ad minim</p>
    <p class="quote two">lorem ipsum dolor sit amet, consectetur adipiscing elit,&nbsp; eiusmod tempor incididunt et dolore gna aliqua. enim ad minim</p>
    <p class="quote three">lorem ipsum dolor sit amet, consectetur adipiscing elit,&nbsp; eiusmod tempor incididunt et dolore gna aliqua. enim ad minim</p>

    <div class="rating one" aria-label="5 out of 5">
      <svg viewBox="0 0 24 18"><polygon points="5,1 19,1 24,6 12,18 0,6" fill="var(--accent)"/></svg>
      <svg viewBox="0 0 24 18"><polygon points="5,1 19,1 24,6 12,18 0,6" fill="var(--accent)"/></svg>
      <svg viewBox="0 0 24 18"><polygon points="5,1 19,1 24,6 12,18 0,6" fill="var(--accent)"/></svg>
      <svg viewBox="0 0 24 18"><polygon points="5,1 19,1 24,6 12,18 0,6" fill="var(--accent)"/></svg>
      <svg viewBox="0 0 24 18"><polygon points="5,1 19,1 24,6 12,18 0,6" fill="var(--accent)"/></svg>
    </div>
    <div class="rating two" aria-label="5 out of 5">
      <svg viewBox="0 0 24 18"><polygon points="5,1 19,1 24,6 12,18 0,6" fill="var(--accent)"/></svg>
      <svg viewBox="0 0 24 18"><polygon points="5,1 19,1 24,6 12,18 0,6" fill="var(--accent)"/></svg>
      <svg viewBox="0 0 24 18"><polygon points="5,1 19,1 24,6 12,18 0,6" fill="var(--accent)"/></svg>
      <svg viewBox="0 0 24 18"><polygon points="5,1 19,1 24,6 12,18 0,6" fill="var(--accent)"/></svg>
      <svg viewBox="0 0 24 18"><polygon points="5,1 19,1 24,6 12,18 0,6" fill="var(--accent)"/></svg>
    </div>
    <div class="rating three" aria-label="5 out of 5">
      <svg viewBox="0 0 24 18"><polygon points="5,1 19,1 24,6 12,18 0,6" fill="var(--accent)"/></svg>
      <svg viewBox="0 0 24 18"><polygon points="5,1 19,1 24,6 12,18 0,6" fill="var(--accent)"/></svg>
      <svg viewBox="0 0 24 18"><polygon points="5,1 19,1 24,6 12,18 0,6" fill="var(--accent)"/></svg>
      <svg viewBox="0 0 24 18"><polygon points="5,1 19,1 24,6 12,18 0,6" fill="var(--accent)"/></svg>
      <svg viewBox="0 0 24 18"><polygon points="5,1 19,1 24,6 12,18 0,6" fill="var(--accent)"/></svg>
    </div>
  </section>

  <section class="location">
    <h2 class="section-title">LOCATION &amp; CONTACT SECTION</h2>

    <div class="contact-line address">
      <svg viewBox="0 0 24 24"><path d="M12 1a8 8 0 0 0-8 8c0 6 8 14 8 14s8-8 8-14a8 8 0 0 0-8-8z" fill="var(--accent)"/><circle cx="12" cy="9" r="3" fill="var(--white)"/></svg>
      <span>Lorem ipsum dolor sit amet</span>
    </div>
    <div class="contact-line mail">
      <svg viewBox="0 0 24 24"><rect x="1" y="5" width="22" height="15" fill="var(--accent)"/><polyline points="1,5 12,14 23,5" fill="none" stroke="var(--white)" stroke-width="1.6"/></svg>
      <span>Lorem ipsum dolor sit amet</span>
    </div>

    <div class="map" role="img" aria-label="Map showing the studio location"></div>

    <form class="contact-form">
      <div class="field name">NAME</div>
      <div class="field email">EMAIL</div>
      <div class="field message">MESSAGE</div>
      <div class="submit">SUBMIT</div>
    </form>
  </section>

  <footer class="site-footer">
    <div class="brand-panel">
      <div class="brand-name">VELOUR<br>DETAILING</div>
    </div>
    <div class="footer-col one">
      <h4>About us</h4>
      <ul><li>Company</li><li>What we do</li><li>Help center</li><li>Contact</li></ul>
    </div>
    <div class="footer-col two">
      <h4>About us</h4>
      <ul><li>Company</li><li>What we do</li><li>Help center</li><li>Contact</li></ul>
    </div>
    <div class="footer-col three">
      <h4>About us</h4>
      <ul><li>Company</li><li>What we do</li><li>Help center</li><li>Contact</li></ul>
    </div>
    <div class="social">
      <span class="social-item">Circlet</span>
      <span class="social-item">Chirp</span>
      <span class="social-item">Lensgram</span>
    </div>
  </footer>

</div>
</body>
</html>
```